Design a New Business Card for Our Company

We are looking for fresh, unique, and a modern business card that reflects our roots as digital marketing agency focused on SEM.

Industry/Entity Type

Marketing

Contact Information for Business Card

looking for very unique out of the box designs. clean and modern that compliments our logo

Requirements
Must have
• colors should match our logo
• Front should have name, address, email, and phone/fax of the person, phone/fax are the same number
• back should have our url

```html
<!DOCTYPE html>
<html lang="en">
<head>
<meta charset="UTF-8">
<title>Brightpath Business Card</title>
<link href="https://fonts.googleapis.com/css2?family=Source+Sans+3:wght@400;600;700&display=swap" rel="stylesheet">
<style>
  :root {
    --page-bg: #e4e6e9;
    --card-bg: #f5f6f8;
    --brand-blue: #5b9bd5;
    --brand-grey: #a9abad;
    --divider-grey: #b9bcc0;
    --text-dark: #3d3f42;
    --white: #ffffff;
  }
  html, body {
    margin: 0;
    width: 1200px;
    height: 900px;
    overflow: hidden;
    background: var(--page-bg);
    font-family: "Source Sans 3", sans-serif;
  }
  .business-card {
    position: absolute;
    left: 83px;
    top: 130px;
    width: 1034px;
    height: 640px;
    background: var(--card-bg);
    box-shadow: 0 10px 30px rgba(0,0,0,0.12);
    overflow: hidden;
  }
  .brand {
    position: absolute;
    left: 0;
    right: 0;
    top: 62px;
    display: flex;
    align-items: center;
    justify-content: center;
    gap: 26px;
  }
  .brand-dot {
    width: 96px;
    height: 96px;
    border-radius: 50%;
    background: var(--brand-blue);
  }
  .brand-name {
    font-size: 124px;
    font-weight: 600;
    color: var(--brand-grey);
    letter-spacing: -2px;
    line-height: 1;
  }
  .person {
    position: absolute;
    left: 70px;
    top: 296px;
  }
  .person-name {
    font-size: 40px;
    font-weight: 600;
    color: var(--brand-blue);
    margin: 0;
    line-height: 1.1;
  }
  .person-role {
    font-size: 29px;
    color: var(--text-dark);
    margin: 6px 0 12px;
  }
  .person-address {
    font-size: 27px;
    color: var(--text-dark);
    line-height: 1.12;
    font-style: normal;
  }
  .contact-list {
    position: absolute;
    right: 66px;
    top: 308px;
    margin: 0;
    padding: 0;
    list-style: none;
    text-align: right;
  }
  .contact-list li {
    display: flex;
    align-items: center;
    justify-content: flex-end;
    gap: 14px;
    font-size: 27px;
    color: var(--text-dark);
    height: 37.5px;
  }
  .contact-list svg {
    width: 18px;
    height: 18px;
    fill: var(--brand-blue);
  }
  .divider {
    position: absolute;
    left: 0;
    right: 0;
    top: 509px;
    height: 21px;
    background: var(--divider-grey);
  }
  .url-band {
    position: absolute;
    left: 0;
    right: 0;
    top: 530px;
    height: 110px;
    background: var(--brand-blue);
    display: flex;
    align-items: center;
    justify-content: center;
    color: var(--white);
    font-size: 28px;
    font-weight: 700;
  }
</style>
</head>
<body>
  <div class="business-card">
    <div class="brand">
      <span class="brand-dot"></span>
      <span class="brand-name">Brightpath</span>
    </div>

    <div class="person">
      <h1 class="person-name">Daniel Morgan</h1>
      <div class="person-role">Managing Director</div>
      <address class="person-address">1234, Address Goes Here<br>Country Name, 123456</address>
    </div>

    <ul class="contact-list">
      <li>123-456-7890
        <svg viewBox="0 0 18 18" aria-label="Mobile"><path d="M5 1h8a1 1 0 0 1 1 1v14a1 1 0 0 1-1 1H5a1 1 0 0 1-1-1V2a1 1 0 0 1 1-1zm1 2v10h6V3zm3 11a1 1 0 1 0 0 2 1 1 0 0 0 0-2z"/></svg>
      </li>
      <li>123-456-7890
        <svg viewBox="0 0 18 18" aria-label="Phone"><path d="M1 6c0-2 3.5-3.5 8-3.5S17 4 17 6v1.5h-4V6H5v1.5H1zM4 9h10l2 6H2zm5 1.5a2 2 0 1 0 0 4 2 2 0 0 0 0-4z"/></svg>
      </li>
      <li>123-456-7890
        <svg viewBox="0 0 18 18" aria-label="Fax"><path d="M5 1h8v5H5zM2 7h14v10H2zm3 3v2h3v-2zm5 0v2h3v-2zm-5 3v2h3v-2zm5 0v2h3v-2z"/></svg>
      </li>
      <li>info@youremail.com
        <svg viewBox="0 0 18 18" aria-label="Email"><path d="M1 4h16v11H1zm1.5 1.5L9 10l6.5-4.5z"/></svg>
      </li>
    </ul>

    <div class="divider"></div>
    <div class="url-band">www.brightpath-sem.com</div>
  </div>
</body>
</html>
```